Business card for law firm

Need business card for new law firm. Think confident, authoritative, conservative, but not stuffy or old-fashioned.

Contact Information for Business Card

Content for card - logo (uploaded), plus the following:

Paul Whitcombe (larger font)
Managing Partner (larger font, but not as large as name)
Level 9, 7 Ferris Lane
Sydney NSW 2000
Main Tel 02 9364 2710
Direct Tel 02 8472 3159
Email paul@qvlegal.com.au
www.qvlegal.com.au

Letterhead design should include logo plus:
Level 9, 7 Ferris Lane
Sydney NSW 2000
Tel 02 8472 3159
www.qvlegal.com.au

```html
<!DOCTYPE html>
<html lang="en">
<head>
<meta charset="utf-8">
<title>Quayvale Legal – Business Card</title>
<link href="https://fonts.googleapis.com/css2?family=Marcellus&family=Jost:wght@400;600&display=swap" rel="stylesheet">
<style>
  :root {
    --backdrop: #3a3a3c;
    --card: #ebebeb;
    --navy: #0f1f5c;
    --ink: #111111;
    --text: #2b2b2b;
    --rule: #555555;
  }
  * { box-sizing: border-box; margin: 0; padding: 0; }
  html, body {
    width: 1200px; height: 1000px; overflow: hidden;
    background: var(--backdrop);
  }
  .canvas {
    position: relative; width: 1200px; height: 1000px;
  }
  .card {
    position: absolute; left: 290px; width: 620px; height: 379px;
    background: var(--card); border-radius: 22px;
    box-shadow: 0 10px 26px rgba(0,0,0,0.35);
  }
  .card--front { top: 92px; }
  .card--back { top: 530px; }

  .brand {
    display: flex; flex-direction: column; align-items: center;
  }
  .brand__mark {
    width: 62px; height: 62px; background: var(--navy);
  }
  .brand__name {
    font-family: "Marcellus", serif; font-weight: 400;
    color: var(--ink); text-transform: uppercase;
    letter-spacing: 0.06em; white-space: nowrap;
  }

  .card--front .brand {
    position: absolute; left: 0; right: 0; top: 108px;
  }
  .card--front .brand__name { font-size: 44px; margin-top: 26px; }

  .card--back .brand {
    position: absolute; left: 28px; width: 270px; top: 118px;
  }
  .card--back .brand__mark { width: 46px; height: 46px; }
  .card--back .brand__name { font-size: 28px; margin-top: 20px; }

  .divider {
    position: absolute; left: 316px; top: 92px; width: 2px; height: 196px;
    background: var(--rule);
  }
  .divider__accent {
    position: absolute; left: 0; top: 0; width: 3px; height: 36px;
    background: var(--navy);
  }

  .contact {
    position: absolute; left: 334px; top: 90px;
    font-family: "Jost", sans-serif; color: var(--text);
    font-size: 14.5px; line-height: 1.3;
  }
  .contact__name {
    font-weight: 600; font-size: 22px; color: var(--navy);
    text-transform: uppercase; letter-spacing: 0.01em; line-height: 1.1;
  }
  .contact__title { font-size: 16px; margin-bottom: 10px; }
  .contact__address { margin-bottom: 12px; }
  .contact__line { display: flex; align-items: center; gap: 5px; }
  .contact__label { font-weight: 600; color: var(--navy); }
  .contact__icon { width: 14px; height: 14px; flex: none; }
  .contact__web strong { font-weight: 600; color: var(--navy); }
</style>
</head>
<body>
<main class="canvas">

  <section class="card card--front" aria-label="Card front">
    <div class="brand">
      <div class="brand__mark"></div>
      <div class="brand__name">Quayvale Legal</div>
    </div>
  </section>

  <section class="card card--back" aria-label="Card back">
    <div class="brand">
      <div class="brand__mark"></div>
      <div class="brand__name">Quayvale Legal</div>
    </div>

    <div class="divider"><span class="divider__accent"></span></div>

    <div class="contact">
      <div class="contact__name">Paul Whitcombe</div>
      <div class="contact__title">Managing Partner</div>
      <div class="contact__address">Level 9, 7 Ferris Lane<br>Sydney NSW 2000</div>
      <div class="contact__line"><span class="contact__label">Main Tel</span> 02 9364 2710</div>
      <div class="contact__line"><span class="contact__label">Direct Tel</span> 02 8472 3159</div>
      <div class="contact__line">
        <svg class="contact__icon" viewBox="0 0 14 14" aria-hidden="true">
          <rect x="1" y="3" width="12" height="8" fill="#2f4c9c"/>
          <path d="M1 3 L7 8 L13 3" fill="none" stroke="#ffffff" stroke-width="1.2"/>
        </svg>
        paul@qvlegal.com.au
      </div>
      <div class="contact__line contact__web">
        <svg class="contact__icon" viewBox="0 0 14 14" aria-hidden="true">
          <circle cx="7" cy="7" r="6" fill="#2f6fc0"/>
          <path d="M1 7 H13 M7 1 V13 M7 1 C3 4 3 10 7 13 M7 1 C11 4 11 10 7 13" fill="none" stroke="#ffffff" stroke-width="0.8"/>
        </svg>
        www.<strong>qvlegal.com</strong>.au
      </div>
    </div>
  </section>

</main>
</body>
</html>
```